Business Card Design Project

This is the first time we use our new logo. We need a business card that we can use both on our institutional corporate relationships and also that works for our staff that deals with consumers directly.

VELUNDA is a new company dedicated to empower consumers and to provide them with the best choices for specialized health care using the latest telemedicine technology (medicine at a distance via videoconference).

We want to print this cards in high quality materials and process. We will like designs that allow us to use UV spot varnish and other techniques that will differentiate us.

We are including Two different versions of Color logos. In addition we are including white over black background logos. Those can be used replacing the black for a color.

Please note this is the first time we will be creating any corporate materials with our new logo and colors.

Target Market(s)

34+ consumers of medium high and high socioeconomic levels.

Industry/Entity Type

Health

Requirements
Must have
• Our logo on its original colors
Should not have
• Any other graphical element or design that is not our logo

```html
<!DOCTYPE html>
<html lang="en">
<head>
<meta charset="utf-8">
<title>VELUNDA Business Card</title>
<link href="https://fonts.googleapis.com/css2?family=Montserrat:wght@600;700&family=Arimo:wght@400&display=swap" rel="stylesheet">
<style>
  :root{
    --page:#ececec;
    --card:#ffffff;
    --navy:#1b5179;
    --teal:#00a99a;
    --sky:#5ab4de;
    --ink:#222222;
    --shadow:rgba(0,0,0,.18);
  }
  *{margin:0;padding:0;box-sizing:border-box}
  html,body{width:1200px;height:1057px;overflow:hidden;background:var(--page)}
  body{position:relative;font-family:"Arimo",Arial,sans-serif;color:var(--ink)}
  .card{
    position:absolute;left:170px;width:860px;height:491px;
    background:var(--card);box-shadow:0 6px 18px var(--shadow);
  }
  .card--front{top:25px}
  .card--back{top:541px}

  .brand-mark{position:absolute;border-radius:50%;background:var(--teal)}
  .card--front .brand-mark{left:70px;top:160px;width:170px;height:170px}
  .wordmark{
    position:absolute;font-family:"Montserrat",Arial,sans-serif;font-weight:700;
    color:var(--navy);letter-spacing:.06em;line-height:1;
  }
  .card--front .wordmark{right:60px;top:60px;font-size:92px}

  .person{position:absolute;right:60px;top:180px;text-align:right;font-family:"Montserrat",Arial,sans-serif}
  .person__name{font-weight:700;color:var(--navy);font-size:26px}
  .person__title{font-weight:600;color:var(--teal);font-size:20px;margin-top:2px}

  .contact{position:absolute;right:60px;top:270px;list-style:none;font-size:19px;line-height:30px;text-align:right}
  .contact li{display:flex;align-items:center;justify-content:flex-end;gap:8px}
  .contact svg{width:16px;height:16px;fill:none;stroke:var(--navy);stroke-width:2}
  .address{position:absolute;right:60px;bottom:40px;font-size:19px}

  .card--back .brand-mark{left:150px;top:150px;width:110px;height:110px}
  .card--back .wordmark{left:295px;top:160px;font-size:96px}
  .web{
    position:absolute;left:0;right:0;top:340px;text-align:center;
    font-family:"Montserrat",Arial,sans-serif;font-weight:600;font-size:26px;letter-spacing:.32em;color:var(--ink)
  }
  .web__name{color:var(--navy)}
</style>
</head>
<body>
  <section class="card card--front">
    <span class="brand-mark" aria-hidden="true"></span>
    <div class="wordmark">VELUNDA</div>
    <div class="person">
      <div class="person__name">Your Name</div>
      <div class="person__title">Title</div>
    </div>
    <ul class="contact">
      <li><svg viewBox="0 0 16 16"><path d="M4 2l3 3-2 2a9 9 0 0 0 4 4l2-2 3 3-2 2C7 14 2 9 2 4z"/></svg>012-555-0147</li>
      <li><svg viewBox="0 0 16 16"><path d="M4 2l3 3-2 2a9 9 0 0 0 4 4l2-2 3 3-2 2C7 14 2 9 2 4z"/></svg>012-555-0147</li>
      <li><svg viewBox="0 0 16 16"><rect x="1.5" y="3.5" width="13" height="9"/><path d="M1.5 3.5l6.5 5 6.5-5"/></svg>name@velunda.com</li>
      <li><svg viewBox="0 0 16 16"><circle cx="8" cy="8" r="6.5"/><path d="M1.5 8h13M8 1.5c3 3 3 10 0 13M8 1.5c-3 3-3 10 0 13"/></svg>www.velunda.com</li>
    </ul>
    <div class="address">Street Name, City Name, State, City Zip Code</div>
  </section>

  <section class="card card--back">
    <span class="brand-mark" aria-hidden="true"></span>
    <div class="wordmark">VELUNDA</div>
    <div class="web">www.<span class="web__name">velunda</span>.com</div>
  </section>
</body>
</html>
```